Looking for someone to design a business card for my plumbing business Quandor Plumbing Solutions I want the background also to be black, must attract clients. If possible I want the front to be the logo and the back to show maybe the details.

Target Market(s)

Clients

Industry/Entity Type

Plumbing maintenance

Contact Information for Business Card

Name: Felix, Contact: 0461 539 207, Email: quandorplumbingsolutions@mailbrook.example, Licence number 728093K

Font styles to use
Other font styles liked:
• as per logo maybe?

Colors

Designer to choose colors to be used in the design.

Requirements
Nice to have
• stating the service I provide, emergency plumbing, plumbing maintenance, drainage maintenance, block sewer and stormwater, camera and locating.

```html
<!DOCTYPE html>
<html lang="en">
<head>
<meta charset="utf-8">
<title>Quandor Plumbing Solutions – Business Card</title>
<link rel="stylesheet" href="https://fonts.googleapis.com/css2?family=Raleway:wght@400;500;800&display=swap">
<style>
  :root {
    --stage: #3a3a3a;
    --card: #1e1e1f;
    --blue: #4a8fd6;
    --white: #ffffff;
    --muted: #e6e6e6;
  }
  * { box-sizing: border-box; margin: 0; padding: 0; }
  html, body { width: 1200px; height: 875px; overflow: hidden; }
  body {
    background: var(--stage);
    font-family: "Raleway", sans-serif;
    color: var(--white);
    position: relative;
  }
  .card {
    position: absolute;
    width: 560px;
    height: 320px;
    background: var(--card);
    border-radius: 18px;
    box-shadow: 0 14px 30px rgba(0,0,0,.35);
    display: flex;
    flex-direction: column;
    align-items: center;
  }
  .card--front { left: 60px; top: 110px; }
  .card--back { left: 580px; top: 440px; }

  .brand-name {
    font-weight: 800;
    color: var(--white);
    text-transform: uppercase;
    text-align: center;
    letter-spacing: .02em;
    line-height: 1.1;
  }
  .card--front .brand-name { margin-top: 78px; font-size: 34px; }
  .card--back .brand-name { margin-top: 52px; font-size: 26px; }

  .services {
    margin-top: 52px;
    text-align: center;
    font-size: 15px;
    line-height: 1.55;
    color: var(--muted);
  }
  .services .dot {
    display: inline-block;
    width: 5px; height: 5px;
    border-radius: 50%;
    background: var(--blue);
    vertical-align: middle;
    margin: 0 8px;
  }

  .details {
    margin-top: 46px;
    display: flex;
    align-items: center;
    gap: 18px;
  }
  .person { text-align: right; font-size: 14px; line-height: 1.35; }
  .person__name {
    font-weight: 800;
    font-size: 24px;
    color: var(--blue);
    text-transform: uppercase;
    line-height: 1.1;
  }
  .divider { width: 1.5px; height: 74px; background: var(--blue); }
  .contact { list-style: none; font-size: 13.5px; line-height: 1.75; }
  .contact li { display: flex; align-items: center; gap: 8px; }
  .contact svg { width: 12px; height: 12px; flex: none; }
  .social-dot {
    width: 11px; height: 11px; border-radius: 50%;
    background: var(--blue); flex: none;
  }
</style>
</head>
<body>

<section class="card card--front" aria-label="Card front">
  <p class="brand-name">Quandor<br>Plumbing Solutions</p>
  <p class="services">
    Emergency plumbing<span class="dot"></span>Plumbing maintenance<span class="dot"></span>Drainage maintenance<br>
    Block sewer and stormwater<span class="dot"></span>Camera and locating
  </p>
</section>

<section class="card card--back" aria-label="Card back">
  <p class="brand-name">Quandor<br>Plumbing Solutions</p>
  <div class="details">
    <div class="person">
      <p class="person__name">Felix</p>
      <p>Founder &amp; CEO</p>
      <p>Licence number 728093K</p>
    </div>
    <div class="divider"></div>
    <ul class="contact">
      <li>
        <svg viewBox="0 0 24 24" aria-hidden="true"><path fill="#4a8fd6" d="M6.6 10.8a15 15 0 0 0 6.6 6.6l2.2-2.2a1 1 0 0 1 1-.25 11.4 11.4 0 0 0 3.6.57 1 1 0 0 1 1 1V20a1 1 0 0 1-1 1A17 17 0 0 1 3 4a1 1 0 0 1 1-1h3.5a1 1 0 0 1 1 1c0 1.25.2 2.45.57 3.57a1 1 0 0 1-.25 1z"/></svg>
        0461 539 207
      </li>
      <li>
        <svg viewBox="0 0 24 24" aria-hidden="true"><path fill="#4a8fd6" d="M2 5h20v14H2z"/><path d="M2 5l10 8 10-8" fill="none" stroke="#1e1e1f" stroke-width="2"/></svg>
        quandorplumbingsolutions@mailbrook.example
      </li>
      <li>
        <span class="social-dot"></span>
        @QuandorPlumbingSolutions
      </li>
    </ul>
  </div>
</section>

</body>
</html>
```